Business Card - high end, modern health care

Hey designers!

We need a double sided business card for the boutique, cutting edge physical therapy rehabilitation centre in Sydney's Northern Beaches.

With the most qualified physios in the area The Harbourview Motion Clinic does what other physiotherapy practices do not, we take our time with our patients giving them longer appointments, better physios and therefor faster results!

We guarantee that the service people receive at THMC will be unparalleled.

Hence we need a business card to reflect our modern, boutique, high end service. The final design needs to reflect that we are in a class of our own yet with the feel of beachside retreat.

Below I have attached our logo in both blue on white and white on blue. The exact colour is;
and the font that we have used in our logo is Tex Gyre Aventador.

I like the idea of the blue as the main colour as it is more eye catching and our signage onto the main road will be in this blue and in the interest of consistency across marketing the blue needs to be a part of the design. However I would appreciate a few designs onto a wooden background as this is a visual theme within the fitout of the practice.

The design needs to be of standard size (91x55mm).

Target Market(s)

We target people who have an end outcome in mind and those who have had poor experiences with other providers and ensure that everyone gets the care that they deserve with a premium service that is tailored to the individuals circumstances. As a premium service, the target market is highly educated, business and tech savvy with the additional target market of elderly people who have self funded their retirement and see value in paying for the best ongoing rehabilitation to maintain independence.

Industry/Entity Type

Physical Therapy

Contact Information for Business Card

Name, designation( Titled Musculoskeletal Physiotherapist... there will also be those in the company that have multiple designations ie 5 or 6 words long), phone number, email, facebook, instagram, address

Font styles to use
Sans Serif

Colors

Designer to choose colors to be used in the design.

Requirements
Must have
• Front - The logo as large as possible, blue or wooden theme, and all of the important details.
• Back - A blank space/lines on which to write appointment times (no "Appointment, date, time" etc.)
Nice to have
• facebook url
• logos for facebook and instagram
• Mini logos for the phone and email?

```html
<!DOCTYPE html>
<html lang="en">
<head>
<meta charset="utf-8">
<title>The Harbourview Motion Clinic – Business Card</title>
<link rel="stylesheet" href="https://fonts.googleapis.com/css2?family=Montserrat:wght@600;700&display=swap">
<style>
  :root {
    --brand-blue: #0f58a6;
    --card-white: #ffffff;
    --card-grey: #c9c9c9;
    --mark-grey: #bcc2c9;
    --stage: #1f1f1f;
  }
  html, body {
    margin: 0;
    padding: 0;
    width: 1200px;
    height: 960px;
    overflow: hidden;
    background: var(--stage);
  }
  .stage {
    position: relative;
    width: 1200px;
    height: 960px;
    font-family: "Montserrat", sans-serif;
  }
  .card {
    position: absolute;
    width: 600px;
    height: 342px;
    border-radius: 18px;
    overflow: hidden;
  }
  .card--front { left: 321px; top: 108px; background: var(--card-white); }
  .card--back  { left: 320px; top: 493px; background: var(--card-grey); }

  .details {
    position: absolute;
    left: 40px;
    top: 72px;
    color: var(--brand-blue);
    font-weight: 700;
  }
  .details__name { margin: 0; font-size: 23px; line-height: 28px; }
  .details__title { margin: 0; font-size: 15px; line-height: 18px; font-weight: 600; }
  .details__address { margin: 14px 0 0; font-size: 14.5px; line-height: 19px; font-style: normal; }
  .contacts { list-style: none; margin: 14px 0 0; padding: 0; font-size: 14.5px; line-height: 19px; }
  .contacts li { display: flex; align-items: center; gap: 10px; }
  .contacts svg { width: 13px; height: 13px; flex: none; fill: var(--brand-blue); }

  .brand-panel {
    position: absolute;
    left: 283px;
    top: 0;
    width: 317px;
    height: 342px;
    background: var(--brand-blue);
    display: flex;
    flex-direction: column;
    align-items: center;
    padding-top: 104px;
    box-sizing: border-box;
  }
  .brand-panel__name {
    margin: 0;
    color: var(--card-white);
    font-size: 24px;
    line-height: 27px;
    font-weight: 700;
    text-align: center;
    letter-spacing: 0.5px;
  }
  .brand-panel__dot {
    margin-top: 22px;
    width: 100px;
    height: 100px;
    border-radius: 50%;
    background: var(--card-white);
  }

  .back-mark {
    position: absolute;
    left: 322px;
    top: 0;
    width: 340px;
    height: 340px;
    border-radius: 50%;
    background: var(--mark-grey);
  }
</style>
</head>
<body>
<main class="stage">
  <section class="card card--front" aria-label="Card front">
    <div class="details">
      <h1 class="details__name">DANIEL MARSH</h1>
      <p class="details__title">CEO/FOUNDER</p>
      <address class="details__address">42 Pittwater Road<br>Manly, NSW 2095</address>
      <ul class="contacts">
        <li>
          <svg viewBox="0 0 16 16" aria-hidden="true"><path d="M3.5 1l2.5 3-1.5 2c1 2 3 4 5 5l2-1.5 3 2.5-1.5 2.5C7 15 1 9 1 2.5z"/></svg>
          02 9555 0147
        </li>
        <li>
          <svg viewBox="0 0 16 16" aria-hidden="true"><path d="M1 3h14v10H1zM2 4.2v.6l6 4 6-4v-.6z"/></svg>
          daniel@harbourview.com
        </li>
        <li>
          <svg viewBox="0 0 16 16" aria-hidden="true"><circle cx="8" cy="8" r="7"/><path d="M1 8h14M8 1v14" stroke="#fff" stroke-width="1.2"/></svg>
          www.harbourview.com
        </li>
        <li>
          <svg viewBox="0 0 16 16" aria-hidden="true"><rect x="1" y="1" width="14" height="14" rx="1.5"/></svg>
          /harbourviewmotion
        </li>
        <li>
          <svg viewBox="0 0 16 16" aria-hidden="true"><rect x="1" y="1" width="14" height="14" rx="3"/></svg>
          @harbourview
        </li>
      </ul>
    </div>
    <div class="brand-panel">
      <p class="brand-panel__name">THE HARBOURVIEW<br>MOTION CLINIC</p>
      <div class="brand-panel__dot" aria-hidden="true"></div>
    </div>
  </section>

  <section class="card card--back" aria-label="Card back">
    <div class="back-mark" aria-hidden="true"></div>
  </section>
</main>
</body>
</html>
```